Business card for builder specialising in renovations.

Need a card for our building business. Business name is under Martin Powles.
Have licence number on card ( 527691K)
Contact number (0400 382 415)
Want to work on logo for some business cards and shirts - something with MP or MPB or open to ideas??
No animations, No hammers. Something sharp and eye catching.
Highlight that we are a renovation specialist. Simple on front with extra details on back with some lines to jot down things.

Target Market(s)

Renovators

Industry/Entity Type

Building

Contact Information for Business Card

2 sided with room on back to jot things down.
Extra details on back so front can be simple ..like, renovations, bathrooms, decks, extensions, new builds,

Logo Text

MP

Font styles to use
Serif

Requirements
Must have
• Eye catching design .
• Name : Martin powles
• Licence number
• Contact number - 0400382415
Nice to have
• Some logo design that we can carry through to other forms of advertising
• Local builder
• Quality work
Should not have
• No animations

```html
<!DOCTYPE html>
<html lang="en">
<head>
<meta charset="utf-8">
<title>Martin Powles Builder – Business Card</title>
<link href="https://fonts.googleapis.com/css2?family=Michroma&family=Open+Sans:wght@600;700;800&display=swap" rel="stylesheet">
<style>
  :root {
    --backdrop: #e9e9e7;
    --card-white: #ececec;
    --card-black: #000000;
    --ink-grey: #58595b;
    --mid-grey: #8c8c8e;
    --light-grey: #a7a9ac;
    --accent-blue: #1b95c9;
    --text-white: #f2f2f2;
  }
  * { box-sizing: border-box; margin: 0; padding: 0; }
  html, body {
    width: 1200px; height: 900px; overflow: hidden;
    background: var(--backdrop);
  }
  .sheet {
    position: relative; width: 1200px; height: 900px;
    display: flex; flex-direction: column; align-items: center; justify-content: center; gap: 40px;
  }
  .card {
    position: relative; width: 700px; height: 400px; overflow: hidden;
    box-shadow: 0 2px 8px rgba(0,0,0,0.15);
  }

  /* Services side */
  .card--services { background: var(--card-white); }
  .services-mark {
    position: absolute; left: 40px; top: 110px; width: 240px; height: 180px;
    display: flex; flex-direction: column; align-items: center; justify-content: center; gap: 14px;
  }
  .services-mark__ring {
    width: 92px; height: 92px; border-radius: 50%;
    border: 5px solid var(--mid-grey);
  }
  .services-mark__name {
    font-family: "Open Sans", sans-serif; font-weight: 800; font-size: 26px;
    color: var(--mid-grey);
  }
  .services-list {
    position: absolute; left: 300px; top: 66px; width: 380px;
    font-family: "Michroma", sans-serif; color: var(--ink-grey);
    line-height: 1; list-style: none;
  }
  .services-list li { white-space: nowrap; }
  .services-list .s-renovations { font-size: 23px; letter-spacing: 2px; }
  .services-list .s-bathrooms { font-size: 26px; letter-spacing: 1px; margin-top: 4px; }
  .services-list .s-decks { font-size: 64px; margin-top: 6px; color: #4a4b4d; }
  .services-list .s-extensions { font-size: 34px; margin-top: 4px; }
  .services-list .s-newbuilds { font-size: 23px; letter-spacing: 1px; margin-top: 6px; }

  /* Contact side */
  .card--contact { background: var(--card-black); }
  .contact-shapes { position: absolute; inset: 0; }
  .contact-header {
    position: absolute; left: 68px; top: 24px;
    font-family: "Open Sans", sans-serif; font-weight: 700; font-size: 20px;
  }
  .contact-header .first { color: var(--accent-blue); }
  .contact-header .last { color: var(--mid-grey); }
  .contact-details {
    position: absolute; left: 60px; top: 180px;
    font-family: "Open Sans", sans-serif; color: var(--text-white);
  }
  .contact-details .phone {
    display: flex; align-items: center; gap: 8px; font-size: 19px; font-weight: 600;
  }
  .contact-details .licence { font-size: 16px; font-weight: 700; margin-top: 6px; }
  .contact-details .licence span { font-weight: 600; }
  .brand-block {
    position: absolute; left: 360px; top: 140px; width: 300px;
    display: flex; flex-direction: column; align-items: center; gap: 14px;
  }
  .brand-block__ring {
    width: 80px; height: 80px; border-radius: 50%;
    border: 5px solid var(--mid-grey);
  }
  .brand-block__name {
    font-family: "Open Sans", sans-serif; font-weight: 800; font-size: 36px;
    color: var(--mid-grey); white-space: nowrap;
  }
</style>
</head>
<body>
<main class="sheet">

  <section class="card card--services" aria-label="Card back: services">
    <div class="services-mark">
      <div class="services-mark__ring"></div>
      <div class="services-mark__name">Martin Powles</div>
    </div>
    <ul class="services-list">
      <li class="s-renovations">RENOVATIONS</li>
      <li class="s-bathrooms">BATHROOMS</li>
      <li class="s-decks">DECKS</li>
      <li class="s-extensions">EXTENSIONS</li>
      <li class="s-newbuilds">NEW BUILDS ETC</li>
    </ul>
  </section>

  <section class="card card--contact" aria-label="Card front: contact">
    <svg class="contact-shapes" width="700" height="400" viewBox="0 0 700 400" aria-hidden="true">
      <polygon points="16,18 52,18 16,54" fill="var(--accent-blue)"/>
      <polygon points="52,18 52,54 16,54" fill="var(--light-grey)"/>
      <polygon points="0,318 300,318 288,352 0,352" fill="var(--mid-grey)"/>
      <polygon points="300,352 700,352 700,400 284,400" fill="var(--accent-blue)"/>
    </svg>

    <div class="contact-header"><span class="first">Martin</span> <span class="last">Powles</span></div>

    <div class="contact-details">
      <div class="phone">
        <svg width="16" height="16" viewBox="0 0 24 24" aria-hidden="true">
          <path fill="var(--accent-blue)" d="M6.6 10.8c1.4 2.8 3.8 5.1 6.6 6.6l2.2-2.2c.3-.3.7-.4 1-.2 1.1.4 2.3.6 3.6.6.6 0 1 .4 1 1V20c0 .6-.4 1-1 1C10.6 21 3 13.4 3 4c0-.6.4-1 1-1h3.5c.6 0 1 .4 1 1 0 1.3.2 2.5.6 3.6.1.3 0 .7-.2 1z"/>
        </svg>
        0400 382 415
      </div>
      <div class="licence">License No- <span>527691K</span></div>
    </div>

    <div class="brand-block">
      <div class="brand-block__ring"></div>
      <div class="brand-block__name">Martin Powles</div>
    </div>
  </section>

</main>
</body>
</html>
```